Harborline Auto LLC

Car Dealer Customer Service
Address: 2874 Cresthaven Road, Shelbyville, TN 37162
web: www.harborlineautoxq.net
email: harborlineautoxq@mailnest.example
Phone: (931) 555-0148
Phone: (629) 555-0173

```html
<!DOCTYPE html>
<html lang="en">
<head>
<meta charset="utf-8">
<title>Harborline Auto – Business Card</title>
<link rel="stylesheet" href="https://fonts.googleapis.com/css2?family=Poppins:wght@400;500;600;700&display=swap">
<style>
  :root{
    --backdrop:#2b2b2b;
    --brand-blue:#1d78ad;
    --brand-blue-deep:#14608f;
    --ink-blue:#195e8e;
    --gold:#d9a23a;
    --emblem-light:#eef1f3;
    --paper:#f1f1f1;
    --paper-shade:#e4e4e4;
    --text-dark:#2a2a2a;
    --rule:#c9c9c9;
    --white:#ffffff;
  }
  *{margin:0;padding:0;box-sizing:border-box;}
  html,body{width:1200px;height:1138px;overflow:hidden;background:var(--backdrop);}
  body{position:relative;font-family:"Poppins",sans-serif;}

  .card{position:absolute;border-radius:16px;overflow:hidden;}

  /* Front */
  .card--front{
    left:274px;top:185px;width:623px;height:377px;
    background:linear-gradient(135deg,var(--brand-blue-deep) 0%,var(--brand-blue) 100%);
    color:var(--white);
  }
  .front__emblem{
    position:absolute;left:-82px;top:20px;width:344px;height:344px;border-radius:50%;
    background:radial-gradient(circle at 55% 50%,var(--gold) 0%,var(--gold) 38%,var(--emblem-light) 62%,var(--emblem-light) 100%);
  }
  .front__name{
    position:absolute;right:41px;top:56px;
    font-weight:600;font-size:35px;letter-spacing:0.5px;line-height:1;
  }
  .front__web{
    position:absolute;right:42px;top:322px;
    font-size:15px;font-weight:400;line-height:1;
  }

  /* Back */
  .card--back{
    left:276px;top:607px;width:618px;height:375px;
    background:linear-gradient(180deg,var(--paper) 0%,var(--paper-shade) 100%);
    color:var(--text-dark);
  }
  .back__brand{
    position:absolute;right:30px;top:30px;
    display:flex;flex-direction:column;align-items:center;gap:21px;
  }
  .brand__dot{width:118px;height:118px;border-radius:50%;background:var(--gold);}
  .brand__name{
    font-weight:600;font-size:24px;color:var(--ink-blue);line-height:1;letter-spacing:0.4px;
  }
  .person{position:absolute;left:26px;top:202px;}
  .person__name{font-weight:700;font-size:25px;color:var(--ink-blue);line-height:1.1;}
  .person__role{font-size:15px;font-weight:400;margin-top:3px;}
  .rule{position:absolute;left:26px;top:264px;width:567px;height:1px;background:var(--rule);}

  .contact{position:absolute;display:flex;align-items:center;gap:8px;line-height:1;}
  .contact svg{width:15px;height:15px;flex:none;}
  .contact--phone{font-weight:700;font-size:17px;color:var(--ink-blue);letter-spacing:0.3px;}
  .contact--plain{font-size:16px;font-weight:400;}
  .contact--wide{letter-spacing:1px;}
</style>
</head>
<body>

<section class="card card--front" aria-label="Card front">
  <div class="front__emblem" role="img" aria-label="Large brand emblem decoration"></div>
  <div class="front__name">HARBORLINE AUTO</div>
  <div class="front__web">www.harborlineautoxq.net</div>
</section>

<section class="card card--back" aria-label="Card back">
  <div class="back__brand">
    <div class="brand__dot"></div>
    <div class="brand__name">HARBORLINE AUTO</div>
  </div>

  <div class="person">
    <div class="person__name">Dorian Vellacourt</div>
    <div class="person__role">Managing Director</div>
  </div>

  <div class="rule"></div>

  <div class="contact contact--phone" style="left:26px;top:281px;">
    <svg viewBox="0 0 16 16" fill="none" stroke="var(--gold)" stroke-width="1.3"><circle cx="8" cy="8" r="7"/><path d="M5.3 4.6c.5-.4 1-.3 1.2.2l.5 1.2c.1.4-.1.7-.4.9-.3.2-.3.5-.1.9.4.7 1 1.3 1.7 1.7.4.2.7.2.9-.1.2-.3.5-.5.9-.4l1.2.5c.5.2.6.7.2 1.2-.8.9-2 .9-3.3.1-1.3-.8-2.4-1.900-3.100-3.200-.6-1.200-.6-2.300.3-3z"/></svg>
    931-555-0148
  </div>
  <div class="contact contact--phone" style="left:26px;top:303px;">
    <svg viewBox="0 0 16 16" fill="none" stroke="var(--gold)" stroke-width="1.3"><circle cx="8" cy="8" r="7"/><path d="M5.3 4.6c.5-.4 1-.3 1.2.2l.5 1.2c.1.4-.1.7-.4.9-.3.2-.3.5-.1.9.4.7 1 1.3 1.7 1.7.4.2.7.2.9-.1.2-.3.5-.5.9-.4l1.2.5c.5.2.6.7.2 1.2-.8.9-2 .9-3.3.1-1.3-.8-2.4-1.9-3.1-3.2-.6-1.2-.6-2.3.3-3z"/></svg>
    629-555-0173
  </div>
  <div class="contact contact--plain" style="left:26px;top:331px;">
    <svg viewBox="0 0 16 16" fill="none" stroke="var(--gold)" stroke-width="1.3"><circle cx="8" cy="8" r="7"/><path d="M8 12.2s-2.6-2.7-2.6-4.6a2.6 2.6 0 0 1 5.2 0c0 1.9-2.6 4.6-2.6 4.6z"/><circle cx="8" cy="7.5" r=".9"/></svg>
    2874 Cresthaven Road, Shelbyville, TN 37162
  </div>

  <div class="contact contact--plain contact--wide" style="left:234px;top:281px;">
    <svg viewBox="0 0 16 16" fill="none" stroke="var(--gold)" stroke-width="1.3"><rect x="1.5" y="3.5" width="13" height="9" rx="1"/><path d="M1.8 4l6.2 4.8L14.2 4"/></svg>
    <span style="margin-left:7px">www.harborlineautoxq.net</span>
  </div>
  <div class="contact contact--plain" style="left:234px;top:303px;">
    <svg viewBox="0 0 16 16" fill="none" stroke="var(--gold)" stroke-width="1.2"><circle cx="8" cy="8" r="6.5"/><ellipse cx="8" cy="8" rx="2.8" ry="6.5"/><path d="M1.5 8h13M2.6 4.8h10.8M2.6 11.2h10.8"/></svg>
    <span style="margin-left:7px">harborlineautoxq@mailnest.example</span>
  </div>
</section>

</body>
</html>
```